Mental Health Clinic Website

website for a mental health clinic. two files describing the website are attached, in case of conflicting info the word document is priority.

Target Market(s)

Ohio / Pennsylvania residents

Industry/Entity Type

Health Care

Coding

Coded - Design and coding required

Number of Pages Required

5+ page

Requirements
Must have
• see attached

```html
<!DOCTYPE html>
<html lang="en">
<head>
<meta charset="utf-8">
<title>Dr Halvorsen Serenity Center</title>
<link href="https://fonts.googleapis.com/css2?family=Lato:wght@400;700;900&family=Poppins:wght@400;500;600;700&display=swap" rel="stylesheet">
<style>
:root{
  --blue:#1d5ead;
  --red:#e3252b;
  --green:#3f9a2c;
  --green-dark:#2e7d1f;
  --ink:#222;
  --text:#444;
  --muted:#888;
  --line:#dcdcdc;
  --dark:#141414;
  --white:#fff;
}
*{box-sizing:border-box;margin:0;padding:0}
html,body{width:1200px;height:4959px;overflow:hidden}
body{font-family:"Poppins",sans-serif;color:var(--text);background:var(--white);position:relative}
.section{position:absolute;left:0;width:1200px}
svg{display:block}

/* header */
.site-header{top:0;height:142px;background:var(--white);z-index:5}
.brand{position:absolute;left:92px;top:0;width:210px;height:215px;background:var(--white);border-radius:0 0 105px 105px;box-shadow:0 4px 12px rgba(0,0,0,.12);display:flex;flex-direction:column;align-items:center;justify-content:center;gap:12px}
.brand-dot{width:70px;height:70px;border-radius:50%;background:var(--green)}
.brand-name{font-family:"Lato",sans-serif;font-weight:700;font-size:13px;color:var(--ink);text-align:center}
.support{position:absolute;left:440px;top:26px;display:flex;align-items:center;gap:12px}
.support-label{font-size:17px;font-weight:700;color:var(--red);line-height:1.1}
.support-num{font-size:19px;font-weight:600;color:var(--ink)}
.lang{position:absolute;left:680px;top:26px;display:flex;align-items:center;gap:10px}
.lang-flag{width:40px;height:40px;border-radius:50%;background:linear-gradient(#c8202f 0 50%,#fff 50% 60%,#1d3f8a 60%)}
.lang-label{font-size:17px;font-weight:700;color:var(--red);line-height:1.1}
.lang-val{font-size:17px;color:var(--ink)}
.btn-appoint{position:absolute;left:848px;top:24px;width:262px;height:56px;border-radius:28px;background:var(--blue);color:var(--white);font-size:16px;font-weight:600;display:flex;align-items:center;justify-content:center;gap:10px}
.main-nav{position:absolute;left:378px;top:96px;display:flex;gap:30px;font-size:16px;font-weight:500;color:var(--ink)}

/* hero */
.hero{top:142px;height:660px}
.hero-photo{position:absolute;inset:0;background:linear-gradient(180deg,#3a2a1e 0%,#b8621d 45%,#e79a3a 60%,#6a3d1c 80%,#2a1a10 100%)}
.hero-title{position:absolute;left:93px;top:235px;font-family:"Lato",sans-serif;font-weight:700;font-size:50px;line-height:68px;color:var(--white);letter-spacing:1px}
.wave{position:absolute;left:0;width:1200px}

/* welcome */
.welcome{top:802px;height:820px}
.welcome-title{text-align:center;font-family:"Lato",sans-serif;font-weight:700;margin-top:62px}
.welcome-title .small{display:block;font-size:33px;color:var(--ink)}
.welcome-title .big{display:block;font-size:38px;color:var(--blue);margin-top:4px}
.welcome-title .big span{color:var(--red)}
.welcome-photo{position:absolute;left:132px;top:135px;width:410px;height:410px;border-radius:50%;border:10px solid var(--green);background:radial-gradient(circle at 50% 40%,#d9c8b6,#8a8f96 70%,#5b5f66)}
.welcome-text{position:absolute;left:598px;top:200px;width:510px;font-size:15.5px;line-height:38px;text-align:justify;color:var(--ink)}
.welcome-text p+p{margin-top:6px}
.welcome-foot{position:absolute;left:105px;top:640px;width:990px;font-size:15.5px;line-height:44px;color:var(--ink)}

/* about */
.about{top:1622px;height:700px}
.about-photo{position:absolute;inset:0;background:linear-gradient(180deg,#1d1410 0%,#6e3a18 30%,#c7782e 48%,#3a2a22 65%,#0e0c0c 100%)}
.about-body{position:absolute;left:93px;top:198px;width:480px;color:var(--white)}
.about-body h2{font-family:"Lato",sans-serif;font-size:34px;font-weight:700;margin-bottom:14px}
.about-body p{font-size:15px;line-height:30px}
.langs{display:grid;grid-template-columns:140px 140px;row-gap:10px;margin-top:10px;font-size:15px}
.langs li{list-style:none;display:flex;align-items:center;gap:8px}

/* team */
.team{top:2322px;height:755px;text-align:center}
.team h2{font-family:"Lato",sans-serif;font-size:36px;font-weight:700;color:var(--blue);margin-top:42px}
.team h2 span{color:var(--red)}
.team-intro{width:950px;margin:16px auto 0;font-size:15px;line-height:30px;color:var(--ink)}
.team-row{position:absolute;left:93px;top:182px;display:flex;gap:26px}
.member{width:238px}
.member-photo{height:270px;background:linear-gradient(180deg,#f3f3f3,#d9dde2);box-shadow:0 2px 8px rgba(0,0,0,.15)}
.member h3{font-family:"Lato",sans-serif;font-size:27px;color:var(--blue);margin-top:22px}
.member .role{font-size:16px;font-weight:600;color:var(--ink);margin-top:8px}
.member .bio{font-size:13.5px;line-height:25px;color:var(--text);margin-top:8px}
.btn-red{display:inline-flex;align-items:center;justify-content:center;gap:8px;background:var(--red);color:var(--white);font-weight:600;border-radius:24px}
.member .btn-red{width:168px;height:42px;font-size:15px;margin-top:22px}
.team-arrow{position:absolute;top:302px;width:28px;height:28px;border:2px solid var(--blue);border-radius:50%;display:flex;align-items:center;justify-content:center}

/* services */
.services{top:3077px;height:700px}
.services-photo{position:absolute;inset:0;background:linear-gradient(180deg,#1a1a1a,#2e2e2e 50%,#151515)}
.services h2{position:absolute;width:100%;top:186px;text-align:center;font-family:"Lato",sans-serif;font-size:36px;font-weight:700;color:var(--white)}
.service-menu{position:absolute;left:93px;top:268px;width:262px;background:var(--white);list-style:none;box-shadow:0 4px 12px rgba(0,0,0,.4)}
.service-menu li{height:52px;padding-left:25px;display:flex;align-items:center;font-size:15.5px;color:var(--ink);border-bottom:1px solid var(--line)}
.service-menu li.active{background:var(--red);color:var(--white)}
.service-detail{position:absolute;left:446px;top:270px;width:680px;color:var(--white)}
.service-detail h3{font-family:"Lato",sans-serif;font-size:30px;font-weight:700;letter-spacing:1px}
.service-detail p{font-size:15px;line-height:31px;margin-top:12px}
.service-detail .btn-red{width:175px;height:46px;font-size:15px;margin-top:18px}

/* contact */
.contact{top:3777px;height:745px;text-align:center}
.contact h2{font-family:"Lato",sans-serif;font-size:36px;font-weight:700;color:var(--blue);margin-top:82px}
.contact-cards{position:absolute;top:150px;left:0;width:1200px}
.c-card{position:absolute;width:300px;text-align:center;font-size:16px;line-height:27px;color:var(--ink)}
.c-icon{width:84px;height:84px;border-radius:50%;background:var(--red);margin:0 auto 22px;display:flex;align-items:center;justify-content:center}
.contact-form{position:absolute;left:165px;top:375px;width:870px}
.field{position:absolute;border-bottom:1px solid var(--line);font-size:13px;color:var(--muted);height:48px;display:flex;align-items:center;gap:8px;padding-left:20px;text-align:left}
.field.message{align-items:flex-start;padding-top:16px;height:150px;border:none;border-bottom:1px solid var(--line)}
.contact .btn-submit{position:absolute;left:512px;top:592px;width:176px;height:50px;background:var(--red);color:var(--white);font-size:17px;font-weight:600;display:flex;align-items:center;justify-content:center;gap:10px}

/* footer */
.site-footer{top:4522px;height:437px;background:var(--dark);color:var(--white)}
.foot-brand{position:absolute;left:120px;top:92px;width:130px;display:flex;flex-direction:column;align-items:center;gap:10px}
.foot-dot{width:56px;height:56px;border-radius:50%;background:var(--green)}
.foot-brand-name{font-family:"Lato",sans-serif;font-weight:700;font-size:11px;color:var(--white);text-align:center}
.socials{display:flex;gap:6px}
.socials span{width:24px;height:24px;border-radius:50%;border:1.5px solid var(--white)}
.foot-col{position:absolute;top:104px}
.foot-col h4{font-family:"Lato",sans-serif;font-size:21px;font-weight:700;letter-spacing:.5px;margin-bottom:22px}
.foot-contact li{list-style:none;display:flex;gap:14px;font-size:14px;line-height:22px;margin-bottom:18px}
.foot-links li{list-style:none;font-size:14px;line-height:34px;display:flex;align-items:center;gap:14px}
.foot-links li::before{content:"";width:9px;height:9px;border-radius:50%;background:var(--white)}
.newsletter p{font-size:12.5px;line-height:22px;width:290px}
.newsletter .email{width:285px;height:42px;background:var(--white);color:var(--muted);font-size:12px;padding-left:12px;display:flex;align-items:center;margin-top:18px}
.newsletter .btn-sub{width:128px;height:38px;background:var(--red);font-size:13px;font-weight:700;display:flex;align-items:center;justify-content:center;margin-top:16px}
.foot-rule{position:absolute;left:80px;top:365px;width:1040px;height:1px;background:#444}
.copyright{position:absolute;top:392px;width:100%;text-align:center;font-size:14px}
</style>
</head>
<body>

<header class="section site-header">
  <div class="brand">
    <div class="brand-dot"></div>
    <div class="brand-name">Dr Halvorsen Serenity Center</div>
  </div>
  <div class="support">
    <svg width="40" height="40" viewBox="0 0 24 24"><path fill="#1d5ead" d="M6.6 10.8a15.1 15.1 0 0 0 6.6 6.6l2.2-2.2c.3-.3.7-.4 1-.2 1.1.4 2.3.6 3.6.6.6 0 1 .4 1 1V20c0 .6-.4 1-1 1A17 17 0 0 1 3 4c0-.6.4-1 1-1h3.5c.6 0 1 .4 1 1 0 1.3.2 2.5.6 3.6.1.3 0 .7-.2 1z"/></svg>
    <div><div class="support-label">SUPPORT CALL US</div><div class="support-num">(440) 555-0142</div></div>
  </div>
  <div class="lang">
    <div class="lang-flag"></div>
    <div><div class="lang-label">Language</div><div class="lang-val">English &#9662;</div></div>
  </div>
  <div class="btn-appoint">
    <svg width="18" height="18" viewBox="0 0 24 24"><rect x="3" y="5" width="18" height="16" rx="2" fill="none" stroke="#fff" stroke-width="2"/><path d="M3 10h18M8 3v4M16 3v4" stroke="#fff" stroke-width="2"/></svg>
    MAKE AN APPOINTMENT
  </div>
  <nav class="main-nav">
    <span>HOME</span><span>ABOUT US</span><span>SERVICES</span><span>TREATMENT MODALITIES</span><span>GOOD READS</span><span>CONTACT US</span>
  </nav>
</header>

<section class="section hero">
  <div class="hero-photo" role="img" aria-label="Silhouette meditating by the water at sunset under palm leaves"></div>
  <h1 class="hero-title">DR HALVORSEN<br>SERENITY CENTER</h1>
  <svg class="wave" style="bottom:0" height="70" viewBox="0 0 1200 70" preserveAspectRatio="none">
    <path d="M0 20 C300 80 800 70 1200 0 L1200 70 L0 70 Z" fill="var(--green)"/>
    <path d="M0 38 C300 92 800 86 1200 22 L1200 70 L0 70 Z" fill="#fff"/>
  </svg>
</section>

<section class="section welcome">
  <h2 class="welcome-title"><span class="small">Welcome to</span><span class="big">DR HALVORSEN <span>SERENITY CENTER</span></span></h2>
  <div class="welcome-photo" role="img" aria-label="Woman meditating calmly at a desk with a laptop"></div>
  <div class="welcome-text">
    <p>Each individual is unique with unique personality and unique needs. Therefore we provide individual treatment customized for you or your child. Multiculturalism also informs our practice. We are a full service mental health practice with the capacity to serve adults, children, teens and their parents.</p>
    <p>We provide high quality evidence based treatment and care including medication management, pharmacogenomic testing, individual psychotherapy, group psychotherapy, art therapy, CBT, DBT and trauma therapy. Our providers are experts in treating variety of illnesses such as depression, anxiety, schizophrenia, ADHD, gender identity concerns and PTSD.</p>
  </div>
  <p class="welcome-foot">We are experienced in a variety of methods that help people achieve their psychological goals, and we will discuss with you the best way to attain the health and wellness that you deserve. We are committed to helping you achieve your optimal level of emotional functioning and fulfill a successful life.</p>
</section>

<section class="section about">
  <div class="about-photo" role="img" aria-label="Person seated in meditation facing a sunset over the sea"></div>
  <svg class="wave" style="top:0" height="80" viewBox="0 0 1200 80" preserveAspectRatio="none">
    <path d="M0 0 L1200 0 L1200 40 C800 -10 400 70 0 20 Z" fill="#fff"/>
    <path d="M0 20 C400 70 800 -10 1200 40 L1200 52 C800 4 400 84 0 34 Z" fill="var(--green)"/>
  </svg>
  <div class="about-body">
    <h2>ABOUT US</h2>
    <p>You will find a number of highly specialized &mdash; experienced and caring therapists and psychiatrists in Serenity Center. We provide medication management, and psychotherapy (counseling) across the lifespan &mdash; children, teens and adults.</p>
    <p style="margin-top:10px">Other than English, we speak the following languages</p>
    <ul class="langs">
      <li>&#10148; Spanish</li><li>&#10148; Farsi</li><li>&#10148; German</li><li>&#10148; Hebrew</li>
    </ul>
  </div>
  <svg class="wave" style="bottom:0" height="80" viewBox="0 0 1200 80" preserveAspectRatio="none">
    <path d="M0 40 C400 90 800 10 1200 50 L1200 80 L0 80 Z" fill="#fff"/>
  </svg>
</section>

<section class="section team">
  <h2>OUR <span>TEAM</span></h2>
  <p class="team-intro">We're looking forward to meeting you quasSed ut perspiciatis unde omnis iste natus error sit voluptatem accusantium doloremque eaque ipsa quae ab illo inventore veritatis et quasi architecto beatae vitae dicta sunt explicabo.</p>
  <div class="team-arrow" style="left:30px"><svg width="12" height="12" viewBox="0 0 12 12"><path d="M8 2 L4 6 L8 10" fill="none" stroke="#1d5ead" stroke-width="2"/></svg></div>
  <div class="team-arrow" style="left:1142px"><svg width="12" height="12" viewBox="0 0 12 12"><path d="M4 2 L8 6 L4 10" fill="none" stroke="#1d5ead" stroke-width="2"/></svg></div>
  <div class="team-row">
    <div class="member">
      <div class="member-photo" role="img" aria-label="Portrait of a male doctor in a white coat"></div>
      <h3>Marco Bellini</h3><div class="role">Sed ut perspiciatis</div>
      <p class="bio">Sed ut perspiciatis unde omnis iste natus error sit voluptatem cusantium doloremque</p>
      <div class="btn-red">&#128197; Appointment</div>
    </div>
    <div class="member">
      <div class="member-photo" role="img" aria-label="Portrait of a doctor in a white coat and tie"></div>
      <h3>Elena Varga</h3><div class="role">Sed ut perspiciatis</div>
      <p class="bio">Sed ut perspiciatis unde omnis iste natus error sit voluptatem cusantium doloremque</p>
      <div class="btn-red">&#128197; Appointment</div>
    </div>
    <div class="member">
      <div class="member-photo" role="img" aria-label="Portrait of a female doctor with arms crossed"></div>
      <h3>Tomas Reinholt</h3><div class="role">Sed ut perspiciatis</div>
      <p class="bio">Sed ut perspiciatis unde omnis iste natus error sit voluptatem cusantium doloremque</p>
      <div class="btn-red">&#128197; Appointment</div>
    </div>
    <div class="member">
      <div class="member-photo" role="img" aria-label="Portrait of a female doctor with a stethoscope"></div>
      <h3>Adrian Costa</h3><div class="role">Sed ut perspiciatis</div>
      <p class="bio">Sed ut perspiciatis unde omnis iste natus error sit voluptatem cusantium doloremque</p>
      <div class="btn-red">&#128197; Appointment</div>
    </div>
  </div>
</section>

<section class="section services">
  <div class="services-photo" role="img" aria-label="Child painting at an easel during an art therapy session"></div>
  <svg class="wave" style="top:0" height="80" viewBox="0 0 1200 80" preserveAspectRatio="none">
    <path d="M0 0 L1200 0 L1200 40 C800 -10 400 70 0 20 Z" fill="#fff"/>
    <path d="M0 20 C400 70 800 -10 1200 40 L1200 52 C800 4 400 84 0 34 Z" fill="var(--green)"/>
  </svg>
  <h2>OUR SERVICES</h2>
  <ul class="service-menu">
    <li>Medication management</li><li>Psychotherapy</li><li class="active">Art Therapy</li><li>Treatment Approach</li><li>Treatment Areas</li>
  </ul>
  <div class="service-detail">
    <h3>ART THERAPY</h3>
    <p>Sed ut perspiciatis unde omnis iste natus error sit voluptatem accusantium doloremque laudantium, totam rem aperiam, eaque ipsa quae ab illo inventore veritatis et quasi architecto beatae vitae dicta sunt explicabo. Nemo enim ipsam voluptatem quia voluptas sit aspernatur aut odit aut fugit totam sequi nesciunt.</p>
    <div class="btn-red">READ MORE &#10148;</div>
  </div>
  <svg class="wave" style="bottom:0" height="80" viewBox="0 0 1200 80" preserveAspectRatio="none">
    <path d="M0 30 C400 90 800 10 1200 40 L1200 52 C800 22 400 102 0 42 Z" fill="var(--green)"/>
    <path d="M0 42 C400 102 800 22 1200 52 L1200 80 L0 80 Z" fill="#fff"/>
  </svg>
</section>

<section class="section contact">
  <h2>CONTACT US</h2>
  <div class="contact-cards">
    <div class="c-card" style="left:98px">
      <div class="c-icon"><svg width="34" height="34" viewBox="0 0 24 24"><path fill="#fff" d="M12 2a7 7 0 0 0-7 7c0 5 7 13 7 13s7-8 7-13a7 7 0 0 0-7-7zm0 9.5A2.5 2.5 0 1 1 12 6.5a2.5 2.5 0 0 1 0 5z"/></svg></div>
      4820 Maplecrest Road,<br>Suite 210, Oakridge, OH 44100
    </div>
    <div class="c-card" style="left:448px">
      <div class="c-icon"><svg width="36" height="36" viewBox="0 0 24 24"><rect x="3" y="6" width="18" height="12" fill="none" stroke="#fff" stroke-width="1.8"/><path d="M3 6l9 7 9-7" fill="none" stroke="#fff" stroke-width="1.8"/></svg></div>
      Email:<br>dr.halvorsen@drhsc.com
    </div>
    <div class="c-card" style="left:819px">
      <div class="c-icon"><svg width="34" height="34" viewBox="0 0 24 24"><path fill="#fff" d="M6.6 10.8a15.1 15.1 0 0 0 6.6 6.6l2.2-2.2c.3-.3.7-.4 1-.2 1.1.4 2.3.6 3.6.6.6 0 1 .4 1 1V20c0 .6-.4 1-1 1A17 17 0 0 1 3 4c0-.6.4-1 1-1h3.5c.6 0 1 .4 1 1 0 1.3.2 2.5.6 3.6.1.3 0 .7-.2 1z"/></svg></div>
      Phone:<br>(440) 555-0142
    </div>
  </div>
  <div class="contact-form">
    <div class="field" style="left:0;top:0;width:430px">&#128100; First Name</div>
    <div class="field" style="left:447px;top:0;width:423px">&#128100; Last Name</div>
    <div class="field" style="left:0;top:52px;width:430px">&#9635; Zipcode</div>
    <div class="field message" style="left:447px;top:52px;width:423px">&#9998; Message</div>
    <div class="field" style="left:0;top:104px;width:430px">&#9993; Email Address</div>
    <div class="field" style="left:0;top:156px;width:430px">&#9742; Phone Number</div>
  </div>
  <div class="btn-submit">
    <svg width="18" height="18" viewBox="0 0 24 24"><path fill="#fff" d="M2 21l21-9L2 3v7l15 2-15 2z"/></svg>SUBMIT
  </div>
</section>

<svg class="wave" style="top:4482px;position:absolute" height="50" viewBox="0 0 1200 50" preserveAspectRatio="none">
  <path d="M0 10 C400 50 800 0 1200 26 L1200 50 L0 50 Z" fill="var(--green)"/>
  <path d="M0 24 C400 62 800 14 1200 38 L1200 50 L0 50 Z" fill="var(--dark)"/>
</svg>

<footer class="section site-footer">
  <div class="foot-brand">
    <div class="foot-dot"></div>
    <div class="foot-brand-name">Dr Halvorsen Serenity Center</div>
    <div class="socials"><span></span><span></span><span></span><span></span></div>
  </div>
  <div class="foot-col" style="left:300px">
    <h4>CONTACT US</h4>
    <ul class="foot-contact">
      <li><span>&#9679;</span><span>4820 Maplecrest Road,<br>Suite 210, Oakridge, OH 44100</span></li>
      <li><span>&#9742;</span><span>Phone : (440) 555-0142</span></li>
      <li><span>&#9993;</span><span>Email:<br>dr.halvorsen@drhsc.com</span></li>
    </ul>
  </div>
  <div class="foot-col" style="left:584px">
    <h4>QUICK LINKS</h4>
    <ul class="foot-links"><li>Home</li><li>About Us</li><li>Services</li><li>Good Reads</li><li>Contact</li></ul>
  </div>
  <div class="foot-col newsletter" style="left:778px">
    <h4>SIGN UP FOR NEWSLETTER</h4>
    <p>Stay informed with our latest news, wellness tips and updates from our care team.</p>
    <div class="email">Enter email</div>
    <div class="btn-sub">SUBSCRIPTION</div>
  </div>
  <div class="foot-rule"></div>
  <div class="copyright">2019 &copy; Copyrights. All Rights Reserved</div>
</footer>

</body>
</html>
```